New Web Design Project

Number of Pages Required

1 page

Requirements
Must have
• An Overview / Background of the Business & Services(not for profit rescue animal farm)
• The Target Market / Audience you are trying to reach (animal lovers)
• Design Specifics; any preferences or ideas for Style, Colour, Imagery, etc (no preferences)

```html
<!DOCTYPE html>
<html lang="en">
<head>
<meta charset="utf-8">
<title>Tailwood Animal Care Center</title>
<link href="https://fonts.googleapis.com/css2?family=Fira+Sans:ital,wght@0,400;0,500;0,600;0,700;1,600&family=Open+Sans:wght@400;600;700&display=swap" rel="stylesheet">
<style>
:root{
  --navy:#1f3566;
  --navy-deep:#173061;
  --blue:#3fa9e0;
  --green:#8dc63f;
  --orange:#f2ae2e;
  --yellow:#f6c744;
  --ink:#222831;
  --text:#6b7079;
  --muted:#9aa0a8;
  --line:#e6e8eb;
  --paper:#ffffff;
  --soft:#f4f5f7;
}
*{box-sizing:border-box;margin:0;padding:0}
html,body{width:1200px;height:4196px;overflow:hidden;background:var(--paper)}
body{position:relative;font-family:"Open Sans",sans-serif;color:var(--text)}
.abs{position:absolute}
h1,h2,h3,h4,.heading{font-family:"Fira Sans",sans-serif;color:var(--ink);font-weight:700}
.btn{position:absolute;display:flex;align-items:center;justify-content:center;font-family:"Fira Sans",sans-serif;font-size:10px;font-weight:600;letter-spacing:.08em;text-transform:uppercase;color:#fff;text-decoration:none}
.photo{position:absolute;overflow:hidden}

/* header navigation */
.site-nav{position:absolute;left:0;top:0;width:1200px;height:61px;background:#fff}
.site-nav ul{position:absolute;left:406px;top:25px;display:flex;gap:24px;list-style:none;font-family:"Fira Sans",sans-serif;font-size:9px;font-weight:600;letter-spacing:.05em;color:var(--ink)}
.site-nav li.active{color:var(--blue)}

/* hero */
.hero{position:absolute;top:61px;left:0;width:1200px;height:436px}
.hero-photo{left:0;top:0;width:1200px;height:436px;background:linear-gradient(120deg,#d9cdbf 0%,#b9ada0 40%,#8a8079 60%,#e6e1db 100%)}
.hero-panel{position:absolute;left:0;top:0}
.hero-title{position:absolute;left:0;width:452px;text-align:center;color:#fff;font-size:40px;top:112px;letter-spacing:-.5px}
.hero-sub{position:absolute;left:0;width:452px;text-align:center;color:#fff;font-family:"Fira Sans",sans-serif;font-weight:600;font-size:25px;top:164px}
.hero-sub em{color:var(--blue);font-style:italic}
.hero-text{position:absolute;left:70px;width:312px;text-align:center;color:#d5dcec;font-size:13px;line-height:20px;top:220px}
.btn-light{background:#fff;color:var(--navy)}
.btn-blue{background:var(--blue)}

/* welcome */
.section-title{position:absolute;left:0;width:1200px;text-align:center;font-size:28px;line-height:36px}
.section-sub{position:absolute;left:0;width:1200px;text-align:center;font-size:13px}
.service-card{position:absolute;top:723px;width:232px;height:276px}
.service-card .photo{inset:0}
.service-tag{position:absolute;left:0;bottom:0;width:120px;height:66px;background:var(--navy);padding:16px 0 0 24px;font-family:"Fira Sans",sans-serif;font-size:14px;font-weight:600;line-height:17px;color:#fff}
.service-tag .hl-yellow{color:var(--yellow)}
.service-tag .hl-blue{color:var(--blue)}
.service-tag .hl-green{color:var(--green)}
.text-link{position:absolute;left:0;width:1200px;text-align:center;font-size:9px;font-weight:600;letter-spacing:.08em;text-transform:uppercase;color:var(--blue)}

/* impact */
.impact-title{left:226px;top:1200px;font-size:27px;line-height:36px}
.impact-text{left:226px;top:1284px;width:300px;font-size:11.5px;line-height:17px}
.btn-green{background:var(--green)}

/* campaign */
.campaign-text .eyebrow{font-size:11px;color:var(--blue);font-weight:600}

/* pets grid */
.pet{position:absolute;width:167px;height:168px}
.btn-orange{background:var(--orange)}

/* events */
.event-day{position:absolute;left:226px;font-family:"Fira Sans",sans-serif;font-size:44px;font-weight:400;color:#cfd3d8}
.event-month{position:absolute;left:290px;font-family:"Fira Sans",sans-serif;font-size:12px;color:var(--ink);font-weight:500}
.event-weekday{position:absolute;left:290px;font-size:10px;color:var(--muted)}
.event-title{position:absolute;left:413px;font-size:15px;font-weight:600}
.event-date{position:absolute;left:413px;font-size:11px;color:var(--muted)}
.event-place{position:absolute;left:413px;font-size:11px;color:var(--blue)}
.divider{position:absolute;left:226px;width:746px;height:1px;background:var(--line)}

/* news */
.news-card{position:absolute;top:3390px;width:232px;height:376px;background:#fff;box-shadow:0 1px 4px rgba(0,0,0,.08)}
.news-card .photo{left:0;top:0;width:232px;height:147px}
.news-cat{position:absolute;left:24px;top:170px;font-size:10px;color:var(--blue)}
.news-title{position:absolute;left:24px;top:198px;width:190px;font-size:16px;line-height:20px}
.news-text{position:absolute;left:24px;top:246px;width:190px;font-size:11px;line-height:16px}
.news-date{position:absolute;left:24px;top:336px;font-size:10px;font-weight:600;color:var(--ink)}

/* footer */
.foot-col{position:absolute;top:3914px}
.foot-col h4{font-size:9px;letter-spacing:.1em;text-transform:uppercase;color:var(--ink);font-weight:600;margin-bottom:18px}
.foot-col li{list-style:none;font-size:11px;color:var(--ink);line-height:20px}
.foot-col p{font-size:11px;line-height:18px;color:var(--text)}
.footer-bottom{position:absolute;left:0;top:4101px;width:1200px;height:95px;background:var(--soft)}
</style>
</head>
<body>

<nav class="site-nav">
  <ul>
    <li class="active">HOME</li><li>ADOPT A PET</li><li>DONATIONS</li><li>FEATURES</li><li>SHORTCODES</li><li>POST TYPES</li>
  </ul>
  <svg class="abs" style="left:1046px;top:25px" width="12" height="12" viewBox="0 0 12 12" aria-label="Search"><circle cx="5" cy="5" r="3.6" fill="none" stroke="#222831" stroke-width="1.4"/><line x1="7.6" y1="7.6" x2="11" y2="11" stroke="#222831" stroke-width="1.4"/></svg>
  <a class="btn btn-green" style="left:1072px;top:21px;width:100px;height:20px;font-size:8px">Donate Now</a>
</nav>

<!-- Hero -->
<section class="hero">
  <div class="photo hero-photo" role="img" aria-label="Cat sitting inside a pet carrier on a tiled floor"></div>
  <svg class="hero-panel" width="510" height="436" viewBox="0 0 510 436" aria-hidden="true"><polygon points="0,0 502,0 470,436 0,436" fill="#173061"/></svg>
  <h1 class="hero-title">Paws in Need</h1>
  <p class="hero-sub">we are their <em>voices</em></p>
  <p class="hero-text">Our Shelter has many pets waiting for a new home. Which one is the best fit for you?</p>
  <a class="btn btn-light" style="left:114px;top:293px;width:104px;height:28px">Pet List</a>
  <a class="btn btn-blue" style="left:229px;top:293px;width:109px;height:28px">Donate Now</a>
</section>

<!-- Welcome -->
<h2 class="section-title" style="top:571px">Welcome to the Tailwood<br>Animal Care Center</h2>
<p class="section-sub" style="top:656px">A totally new experience for you and your little friend.</p>

<div class="service-card" style="left:226px">
  <div class="photo" style="background:linear-gradient(150deg,#7b4a2e,#3e2a22 60%,#5a3b2b)" role="img" aria-label="Woman holding a small dog"></div>
  <div class="service-tag"><span class="hl-yellow">Adopt</span><br>or Foster</div>
</div>
<div class="service-card" style="left:483px">
  <div class="photo" style="background:linear-gradient(160deg,#9b5f5a,#6d4a48 45%,#3a302f)" role="img" aria-label="Dog noses peeking from under a striped blanket"></div>
  <div class="service-tag">Donate<br><span class="hl-blue">&amp; Support</span></div>
</div>
<div class="service-card" style="left:740px">
  <div class="photo" style="background:linear-gradient(150deg,#d9cfc0,#b48b62 55%,#8a6a4d)" role="img" aria-label="Two dogs behind a shelter fence"></div>
  <div class="service-tag"><span class="hl-green">Volunteer</span><br>Opportunities</div>
</div>
<p class="text-link" style="top:1035px">Take action to save lives and bring hope for pets in need</p>
<div class="divider" style="left:0;width:1200px;top:1116px"></div>

<!-- Impact -->
<h2 class="abs heading impact-title">Let’s Make a Significant,<br>Lifesaving Impact</h2>
<p class="abs impact-text">Show your love for animals—and help every pet find the loving home they deserve. Learn how we make a significant, lifesaving impact for pets in communities across the country.</p>
<a class="btn btn-green" style="left:226px;top:1359px;width:134px;height:31px">Get Involved</a>
<svg class="abs" style="left:620px;top:1178px" width="370" height="168" viewBox="0 0 370 168" role="img" aria-label="Woman kissing a cat through a shelter cage">
  <defs><linearGradient id="impactPhoto" x1="0" x2="1"><stop offset="0" stop-color="#6b3a34"/><stop offset=".5" stop-color="#b9aba0"/><stop offset="1" stop-color="#d8d1c8"/></linearGradient></defs>
  <path d="M20,30 C60,0 200,4 300,8 C352,10 370,50 360,90 C350,140 300,166 200,162 C110,160 40,168 14,130 C-6,100 0,50 20,30Z" fill="url(#impactPhoto)"/>
  <circle cx="170" cy="128" r="15" fill="#fff"/>
  <polygon points="166,121 166,135 177,128" fill="#3fa9e0"/>
</svg>

<!-- Campaign band -->
<svg class="abs" style="left:0;top:1493px" width="1200" height="349" viewBox="0 0 1200 349" aria-hidden="true">
  <path d="M0,18 L60,10 L120,16 L190,6 L260,14 L340,4 L420,12 L500,8 L580,16 L660,6 L740,12 L820,4 L900,14 L980,6 L1060,12 L1140,4 L1200,10 L1200,332 L1130,340 L1050,334 L970,344 L890,336 L810,346 L730,336 L650,342 L570,334 L490,344 L410,336 L330,344 L250,334 L170,342 L90,336 L0,344Z" fill="#1f3566"/>
</svg>
<div class="abs" style="left:226px;top:1590px;width:140px;height:140px;border-radius:50%;background:radial-gradient(circle at 50% 50%,#e6ddd3,#9a8676 70%,#6a5546)" role="img" aria-label="Small bulldog puppy"></div>
<div class="abs campaign-text" style="left:402px;top:1584px;width:300px">
  <p class="eyebrow">$2500 To Go</p>
  <h3 style="color:#fff;font-size:19px;line-height:24px;margin-top:6px">Help for the Animals Affected by<br>Hurricane Harvey</h3>
  <p style="color:#b8c3da;font-size:11px;line-height:16px;margin-top:8px">Sed ut dolor sit amet marcetur eng elit. Scipe nobias, excepit sagittis leo sit met atrum vestibulum dignissim.</p>
</div>
<a class="btn btn-blue" style="left:402px;top:1716px;width:98px;height:28px">Donate Now</a>
<svg class="abs" style="left:805px;top:1600px" width="120" height="120" viewBox="0 0 120 120" aria-label="71 percent donated">
  <circle cx="60" cy="60" r="54" fill="none" stroke="#2c4477" stroke-width="3"/>
  <circle cx="60" cy="60" r="54" fill="none" stroke="#3fa9e0" stroke-width="3" stroke-dasharray="241 339" transform="rotate(-90 60 60)"/>
  <text x="60" y="62" text-anchor="middle" font-family="Fira Sans,sans-serif" font-size="24" font-weight="700" fill="#fff">71<tspan font-size="10" dy="-10">%</tspan></text>
  <text x="60" y="80" text-anchor="middle" font-family="Open Sans,sans-serif" font-size="9" fill="#fff">Donated</text>
</svg>

<!-- Adopt -->
<h2 class="section-title" style="top:1910px">Adopt or Foster One and<br>Help Save Them All</h2>
<p class="section-sub" style="top:1995px">A totally new experience for you and your little friend.</p>
<div class="pet photo" style="left:226px;top:2065px;background:linear-gradient(160deg,#8a5a3a,#5e8a44)" role="img" aria-label="Bloodhound sitting on grass"></div>
<div class="pet photo" style="left:419px;top:2065px;background:linear-gradient(160deg,#a9c38a,#6d5940)" role="img" aria-label="Terrier mix in a park"></div>
<div class="pet photo" style="left:611px;top:2065px;background:linear-gradient(160deg,#e6c48e,#c58d4e)" role="img" aria-label="Pomeranian puppy"></div>
<div class="pet photo" style="left:804px;top:2065px;background:linear-gradient(160deg,#8b5a35,#3c7a3b)" role="img" aria-label="Collie with a blue bandana"></div>
<div class="pet photo" style="left:226px;top:2254px;background:linear-gradient(160deg,#7da05a,#9a6a3e)" role="img" aria-label="Boxer with a blue bandana"></div>
<div class="pet photo" style="left:419px;top:2254px;background:linear-gradient(160deg,#4e3a2a,#6f8f4a)" role="img" aria-label="Rottweiler with a blue bandana"></div>
<div class="pet photo" style="left:611px;top:2254px;background:linear-gradient(160deg,#c7a67a,#6b9a4f)" role="img" aria-label="Labrador mix on grass"></div>
<div class="pet photo" style="left:804px;top:2254px;background:linear-gradient(160deg,#3d3e5e,#8a6a52)" role="img" aria-label="Long-haired terrier with a blue bandana"></div>
<a class="btn btn-orange" style="left:522px;top:2472px;width:153px;height:31px;color:var(--ink)">Meet All the Pets</a>
<div class="divider" style="left:0;width:1200px;top:2567px"></div>

<!-- Events -->
<h2 class="section-title" style="top:2646px">Take Part in Our Events &amp; Make<br>the World a Better Place</h2>

<span class="event-day" style="top:2768px">20</span>
<span class="event-month" style="top:2786px">January</span>
<span class="event-weekday" style="top:2803px">Sunday</span>
<h4 class="event-title" style="top:2783px">Meet &amp; Greet Adoption Event</h4>
<span class="event-date" style="top:2811px">January 20 - December 20</span>
<a class="btn btn-blue" style="left:868px;top:2796px;width:104px;height:28px">Find Out More</a>
<div class="divider" style="top:2874px"></div>

<span class="event-day" style="top:2894px">20</span>
<span class="event-month" style="top:2912px">January</span>
<span class="event-weekday" style="top:2929px">Sunday</span>
<h4 class="event-title" style="top:2909px">Volunteer as Pet Foster Carer</h4>
<span class="event-date" style="top:2937px">January 20 - December 20</span>
<a class="btn btn-blue" style="left:868px;top:2922px;width:104px;height:28px">Find Out More</a>
<div class="divider" style="top:3002px"></div>

<span class="event-day" style="top:3020px">20</span>
<span class="event-month" style="top:3038px">January</span>
<span class="event-weekday" style="top:3055px">Sunday</span>
<h4 class="event-title" style="top:3035px">Adopt One. Help Thousands</h4>
<span class="event-date" style="top:3063px">January 20 - December 20</span>
<span class="event-place" style="top:3080px">Riverside Green Millbrook</span>
<a class="btn btn-blue" style="left:868px;top:3048px;width:104px;height:28px">Find Out More</a>
<p class="text-link" style="top:3157px">View All Events</p>

<!-- News -->
<svg class="abs" style="left:0;top:3245px" width="1200" height="340" viewBox="0 0 1200 340" aria-hidden="true">
  <path d="M0,0 L1200,0 L1200,322 L1130,330 L1050,322 L970,334 L890,324 L810,336 L730,326 L650,334 L570,322 L490,334 L410,324 L330,336 L250,324 L170,332 L90,322 L0,330Z" fill="#1f3566"/>
</svg>
<h2 class="section-title" style="top:3314px;color:#fff;font-size:26px">Latest Pets News</h2>

<article class="news-card" style="left:226px">
  <div class="photo" style="background:linear-gradient(160deg,#d8c3b0,#6b4a3a)" role="img" aria-label="Woman hugging a puppy"></div>
  <span class="news-cat">Pet Adoption</span>
  <h3 class="news-title">Adopting a Pet: Why<br>and What For?</h3>
  <p class="news-text">Lorem ipsum dolor sit amet, consectetur adipiscing elit. Pellentesque fermentum massa vel enim feugiat gravida. Phasellus...</p>
  <span class="news-date">March 23, 2018</span>
</article>
<article class="news-card" style="left:483px">
  <div class="photo" style="background:linear-gradient(160deg,#9bbd6a,#e6e6e0 55%,#3d5a8a)" role="img" aria-label="Boy playing with a dog on grass"></div>
  <span class="news-cat">Vaccinations</span>
  <h3 class="news-title">Why You Should Vaccinate<br>Your Pet</h3>
  <p class="news-text">Lorem ipsum dolor sit amet, consectetur adipiscing elit. Pellentesque fermentum massa vel enim feugiat gravida. Phasellus...</p>
  <span class="news-date">March 17, 2018</span>
</article>
<article class="news-card" style="left:740px">
  <div class="photo" style="background:linear-gradient(160deg,#e7a766,#c9773a 55%,#f1e4d4)" role="img" aria-label="Ginger cat close up"></div>
  <span class="news-cat">Tips</span>
  <h3 class="news-title">Keeping Your Cat<br>Safe and Healthy</h3>
  <p class="news-text">Duis autem vel eum iriure dolor in hendrerit in vulputate velit esse molestie consequat, vel illum...</p>
  <span class="news-date">March 15, 2018</span>
</article>

<svg class="abs" style="left:590px;top:3797px" width="20" height="6" aria-hidden="true"><circle cx="3" cy="3" r="2.5" fill="#c9cdd2"/><circle cx="14" cy="3" r="2.5" fill="#e2e5e8"/></svg>
<div class="abs" style="left:1172px;top:3733px;width:28px;height:26px;background:#9ba0a6;display:flex;align-items:center;justify-content:center" aria-label="Back to top">
  <svg width="10" height="8" viewBox="0 0 10 8"><polyline points="1,6 5,2 9,6" fill="none" stroke="#fff" stroke-width="1.6"/></svg>
</div>
<div class="divider" style="left:0;width:1200px;top:3858px"></div>

<!-- Footer -->
<footer>
  <div class="foot-col" style="left:226px">
    <h4>Tailwood</h4>
    <ul><li>About Us</li><li>How It Works</li><li>Our Blog</li><li>Contacts</li></ul>
  </div>
  <div class="foot-col" style="left:419px">
    <h4>Adoption Information</h4>
    <ul><li>Adoption Information</li><li>Adopt a Cat</li><li>Adopt a Dog</li><li>Adoption Programs</li></ul>
  </div>
  <div class="foot-col" style="left:614px">
    <h4>Contact Information</h4>
    <p>Address: 48 Alder Lane, Millbrook,<br>NY 10000, United States</p>
    <p style="margin-top:8px">Phone: 1-800-555-0142<br>Email: <span style="color:var(--ink)">hello@tailwood.org</span></p>
  </div>
  <div class="foot-col" style="left:806px">
    <h4>Stay in Touch</h4>
    <p>Get Our Weekly Updates:</p>
  </div>
  <div class="abs" style="left:806px;top:3973px;width:96px;height:28px;border:1px solid var(--line);font-size:9px;color:var(--muted);padding:8px 0 0 10px">Your E-mail</div>
  <a class="btn btn-green" style="left:908px;top:3973px;width:64px;height:28px;font-size:9px">Sign Up</a>
  <div class="footer-bottom">
    <div class="abs" style="left:1158px;top:42px;width:28px;height:22px;background:#b9bec4"></div>
  </div>
</footer>

</body>
</html>
```